Im open to ideas.. I was thinking on my business cards aswell as my logo. a place for my name. email. phone number and abn..

ive attched a file with my business logo. which i dont love the colours.. i was think a dark background with charcoal letters so something along those colour schumes but im open to ideas..

BRM Constructions

```html
<!DOCTYPE html>
<html lang="en">
<head>
<meta charset="utf-8">
<title>BRM Constructions — Business Card</title>
<link href="https://fonts.googleapis.com/css2?family=Montserrat:wght@400;500;600;700&display=swap" rel="stylesheet">
<style>
  :root {
    --backdrop: #e6e4e1;
    --card: #f7f7f6;
    --red: #e3202a;
    --black: #151515;
    --ink: #1c1c1c;
    --white: #ffffff;
  }
  * { margin: 0; padding: 0; box-sizing: border-box; }
  html, body { width: 1200px; height: 1022px; overflow: hidden; }
  body {
    background: var(--backdrop);
    font-family: "Montserrat", Arial, sans-serif;
    color: var(--ink);
    position: relative;
  }
  .card {
    position: absolute;
    left: 150px; top: 251px;
    width: 900px; height: 520px;
    background: var(--card);
    border-radius: 18px;
    overflow: hidden;
    box-shadow: 0 10px 30px rgba(0,0,0,.18);
  }
  .card-bands { position: absolute; left: 0; top: 0; width: 900px; height: 520px; }
  .brand {
    position: absolute; left: 70px; top: 210px;
    display: flex; align-items: center; gap: 16px;
  }
  .brand-mark { width: 26px; height: 26px; background: var(--red); }
  .brand-name {
    font-size: 40px; font-weight: 700; color: var(--black);
    letter-spacing: 1px; line-height: 1; text-transform: uppercase;
  }
  .holder {
    position: absolute; right: 80px; top: 140px; text-align: right;
  }
  .holder-name {
    font-size: 36px; font-weight: 600; color: var(--red);
    letter-spacing: 1px; text-transform: uppercase; line-height: 1.1;
  }
  .holder-role { font-size: 20px; font-weight: 500; color: var(--ink); margin-top: 4px; }
  .divider {
    position: absolute; left: 360px; right: 70px; top: 262px;
    height: 3px; background: var(--red);
  }
  .contacts {
    position: absolute; left: 370px; top: 290px;
    list-style: none; font-size: 20px; line-height: 32px;
  }
  .contacts li { display: flex; align-items: center; gap: 14px; }
  .contacts svg { width: 16px; height: 16px; flex: none; }
  .contacts .web { color: var(--red); }
  .abn {
    position: absolute; right: 40px; bottom: 46px;
    color: var(--white); font-size: 20px; font-weight: 500;
  }
  .abn strong { font-weight: 700; }
</style>
</head>
<body>
  <main class="card">
    <svg class="card-bands" viewBox="0 0 900 520" aria-hidden="true">
      <rect x="0" y="484" width="900" height="36" fill="var(--black)"/>
      <polygon points="620,410 900,410 900,520 580,520 580,484 600,484" fill="var(--red)"/>
    </svg>

    <div class="brand">
      <span class="brand-mark"></span>
      <span class="brand-name">BRM Constructions</span>
    </div>

    <div class="holder">
      <div class="holder-name">Marcus Ellery</div>
      <div class="holder-role">Director</div>
    </div>

    <div class="divider"></div>

    <ul class="contacts">
      <li>
        <svg viewBox="0 0 16 16"><path d="M4 1.5 6.5 4 5 6c1 2 3 4 5 5l2-1.5 2.5 2.5-2 2.5C7 14 2 9 1.5 3.5Z" fill="none" stroke="var(--red)" stroke-width="1.4"/></svg>
        <span>+330 2470-1183</span>
      </li>
      <li>
        <svg viewBox="0 0 16 16"><rect x="1.5" y="3.5" width="13" height="9" fill="none" stroke="var(--red)" stroke-width="1.4"/><path d="M1.5 3.5 8 9l6.5-5.5" fill="none" stroke="var(--red)" stroke-width="1.4"/></svg>
        <span>info@brmconstructions.com</span>
      </li>
      <li>
        <svg viewBox="0 0 16 16"><circle cx="8" cy="8" r="6.5" fill="none" stroke="var(--red)" stroke-width="1.4"/><path d="M1.5 8h13M8 1.5c-3 3.5-3 9.5 0 13M8 1.5c3 3.5 3 9.5 0 13" fill="none" stroke="var(--red)" stroke-width="1.2"/></svg>
        <span>www.<span class="web">brmconstructions</span>.com</span>
      </li>
    </ul>

    <div class="abn"><strong>ABN:</strong> 61 482 730 145</div>
  </main>
</body>
</html>
```